High Tech Real Estate Startup needs a business card

We are developing an innovative real estate marketing product based around advanced search and virtual reality.

We talk to people, we need business cards.

Target Market(s)

The target market is technology professionals and realtors.

Contact Information for Business Card

The information to be included will include

Name
Title
Phone Number
E-mail Address
www.zelquin.com

It should use simple iconography for each one of those fields.

Font styles to use
Other font styles liked:
• Co, Jubilat, Avenir

Colors

Designer to choose colors to be used in the design.

Requirements
Must have
• Clean aesthetic,
• Good use of negative space.
• It should use our company logo, shown in the attached file. It is able to use the negative of that logo (coloured font and white background) and I have attached other acceptable accent colours in a swatch file.
Should not have
• Should not be too busy
• No extraneous text (slogans, tag lines etc)

```html
<!DOCTYPE html>
<html lang="en">
<head>
<meta charset="utf-8">
<title>Zelquin Business Card</title>
<link rel="stylesheet" href="https://fonts.googleapis.com/css2?family=Work+Sans:wght@400;500;600&display=swap">
<style>
  :root {
    --backdrop: #3a322e;
    --card: #1b1b1c;
    --teal: #2bbfc4;
    --ink: #f2f2f2;
  }
  * { margin: 0; padding: 0; box-sizing: border-box; }
  html, body {
    width: 1200px; height: 715px; overflow: hidden;
    background: var(--backdrop);
    font-family: "Work Sans", sans-serif;
  }
  .canvas {
    position: relative; width: 1200px; height: 715px;
    display: flex; align-items: center; justify-content: center; gap: 40px;
  }
  .card {
    position: relative; width: 540px; height: 309px;
    background: var(--card);
    border-bottom: 4px solid var(--teal);
  }
  .logo-square {
    position: absolute; background: var(--teal);
    display: flex; align-items: center; justify-content: center;
    color: #ffffff; font-weight: 500; letter-spacing: 0.04em;
  }
  .card-front .logo-square {
    width: 146px; height: 146px; left: 197px; top: 81px; font-size: 22px;
  }
  .card-back .logo-square {
    width: 130px; height: 130px; left: 52px; top: 89px; font-size: 19px;
  }
  .divider {
    position: absolute; left: 222px; top: 74px;
    width: 2px; height: 160px; background: var(--teal);
  }
  .contact {
    position: absolute; left: 248px; top: 84px; color: var(--ink);
  }
  .contact-name {
    color: var(--teal); font-weight: 600; font-size: 18px;
    letter-spacing: 0.03em; text-transform: uppercase;
  }
  .contact-title { font-size: 13px; margin: 2px 0 10px; }
  .contact-address { font-size: 13px; line-height: 1.35; margin-bottom: 8px; }
  .contact-list { list-style: none; font-size: 13px; line-height: 1.45; }
  .contact-list li { display: flex; align-items: center; gap: 8px; }
  .contact-icon { width: 10px; height: 10px; flex: none; }
</style>
</head>
<body>
<main class="canvas">
  <section class="card card-front" aria-label="Card front">
    <div class="logo-square">ZELQUIN</div>
  </section>

  <section class="card card-back" aria-label="Card back">
    <div class="logo-square">ZELQUIN</div>
    <div class="divider"></div>
    <div class="contact">
      <p class="contact-name">Daniel Rourke</p>
      <p class="contact-title">Director</p>
      <p class="contact-address">417 Alder Creek Rd.<br>Franklin, TN 37064</p>
      <ul class="contact-list">
        <li>
          <svg class="contact-icon" viewBox="0 0 10 10" aria-hidden="true">
            <path d="M2 1 L4 1 L4.6 3 L3.4 3.8 Q4.4 5.8 6.2 6.6 L7 5.4 L9 6 L9 8 Q5 9 2.4 6 Q0.8 3.8 2 1 Z" fill="#2bbfc4"/>
          </svg>
          +1-555-014-2271
        </li>
        <li>
          <svg class="contact-icon" viewBox="0 0 10 10" aria-hidden="true">
            <rect x="0.8" y="2" width="8.4" height="6" fill="none" stroke="#2bbfc4" stroke-width="1"/>
            <path d="M0.8 2 L5 5.4 L9.2 2" fill="none" stroke="#2bbfc4" stroke-width="1"/>
          </svg>
          info@zelquin.com
        </li>
        <li>
          <svg class="contact-icon" viewBox="0 0 10 10" aria-hidden="true">
            <circle cx="5" cy="5" r="4.2" fill="none" stroke="#2bbfc4" stroke-width="1"/>
            <ellipse cx="5" cy="5" rx="1.8" ry="4.2" fill="none" stroke="#2bbfc4" stroke-width="0.8"/>
            <path d="M0.8 5 H9.2" stroke="#2bbfc4" stroke-width="0.8"/>
          </svg>
          www.zelquin.com
        </li>
      </ul>
    </div>
  </section>
</main>
</body>
</html>
```